Brivolt Technologies business card design

We need a business card designed with our new logo. it would be great if the card could communicate it is a technology based company.

Target Market(s)

system integrators

Industry/Entity Type

technology, IOT

Contact Information for Business Card

Name, designation, Address, telephone number, email address

Requirements
Must have
• logo and company name
Nice to have
• something to do with technology

```html
<!DOCTYPE html>
<html lang="en">
<head>
<meta charset="utf-8">
<title>Brivolt Technologies — Business Card</title>
<link href="https://fonts.googleapis.com/css2?family=Open+Sans:ital,wght@0,400;0,700;0,800;1,400&display=swap" rel="stylesheet">
<style>
  :root {
    --stage: #2b2b2b;
    --card: #1b1b1b;
    --accent: #f39200;
    --text: #ffffff;
    --muted: #3a3a3a;
    --brand-dim: #4a4a4a;
  }
  * { box-sizing: border-box; margin: 0; padding: 0; }
  html, body {
    width: 1200px; height: 900px; overflow: hidden;
    background: var(--stage);
    font-family: "Open Sans", Arial, sans-serif;
  }
  .stage {
    width: 1200px; height: 900px;
    display: flex; flex-direction: column; align-items: center; justify-content: center;
    gap: 40px;
  }
  .card {
    position: relative;
    width: 700px; height: 400px;
    background: var(--card);
    border-bottom: 3px solid var(--accent);
    box-shadow: 0 12px 30px rgba(0,0,0,.45);
    overflow: hidden;
  }
  .brand {
    display: flex; align-items: center; gap: 14px;
    font-weight: 800; letter-spacing: 1px; text-transform: uppercase;
  }
  .brand-mark { width: 22px; height: 22px; background: var(--accent); }
  .card-front .brand { position: absolute; left: 48px; top: 48px; font-size: 30px; color: var(--text); }
  .person { position: absolute; left: 48px; top: 150px; }
  .person-name { color: var(--accent); font-weight: 800; font-size: 26px; text-transform: uppercase; }
  .person-role { color: var(--text); font-style: italic; font-size: 17px; margin-top: 2px; }
  .contact { position: absolute; left: 48px; top: 240px; list-style: none; }
  .contact li {
    display: flex; align-items: center; gap: 12px;
    color: var(--text); font-size: 17px; line-height: 30px;
  }
  .contact svg { width: 16px; height: 16px; fill: var(--accent); flex: none; }
  .address {
    position: absolute; right: 48px; bottom: 40px;
    color: var(--text); font-size: 17px; line-height: 26px; text-align: right;
  }
  .card-back { display: flex; align-items: center; justify-content: center; }
  .card-back .brand { font-size: 40px; color: var(--brand-dim); }
  .card-back .brand-mark { width: 30px; height: 30px; background: var(--brand-dim); }
</style>
</head>
<body>
<main class="stage">
  <section class="card card-front">
    <div class="brand"><span class="brand-mark"></span>Brivolt Technologies</div>
    <div class="person">
      <p class="person-name">Darien Colvell</p>
      <p class="person-role">President</p>
    </div>
    <ul class="contact">
      <li>
        <svg viewBox="0 0 24 24" aria-hidden="true"><path d="M6.6 10.8a15 15 0 0 0 6.6 6.6l2.2-2.2a1 1 0 0 1 1-.25 11.4 11.4 0 0 0 3.6.57 1 1 0 0 1 1 1V20a1 1 0 0 1-1 1A17 17 0 0 1 3 4a1 1 0 0 1 1-1h3.5a1 1 0 0 1 1 1c0 1.25.2 2.45.57 3.57a1 1 0 0 1-.25 1z"/></svg>
        555-318-0472
      </li>
      <li>
        <svg viewBox="0 0 24 24" aria-hidden="true"><path d="M2 5h20v14H2z M2 5l10 8 10-8" /><path d="M3 6l9 7 9-7v-.5H3z" fill="#1b1b1b"/></svg>
        info@brivolttechnologies.com
      </li>
      <li>
        <svg viewBox="0 0 24 24" aria-hidden="true"><path d="M12 2a10 10 0 1 0 0 20 10 10 0 0 0 0-20zm6.9 6h-3a15 15 0 0 0-1.3-3.9A8 8 0 0 1 18.9 8zM12 4c.8 1.2 1.5 2.5 1.9 4h-3.8c.4-1.5 1.1-2.8 1.9-4zM4.3 14a8 8 0 0 1 0-4h3.4a16 16 0 0 0 0 4zm.8 2h3a15 15 0 0 0 1.3 3.9A8 8 0 0 1 5.1 16zm3-8h-3a8 8 0 0 1 4.3-3.9A15 15 0 0 0 8.1 8zM12 20c-.8-1.2-1.5-2.5-1.9-4h3.8c-.4 1.5-1.1 2.8-1.9 4zm2.3-6H9.7a14 14 0 0 1 0-4h4.6a14 14 0 0 1 0 4zm.3 5.9a15 15 0 0 0 1.3-3.9h3a8 8 0 0 1-4.3 3.9zm1.7-5.9a16 16 0 0 0 0-4h3.4a8 8 0 0 1 0 4z"/></svg>
        www.brivolttechnologies.com
      </li>
    </ul>
    <address class="address" style="font-style:normal">
      3145 Marlowe Harbor Dr<br>Seacliff CA 92011
    </address>
  </section>

  <section class="card card-back">
    <div class="brand"><span class="brand-mark"></span>Brivolt Technologies</div>
  </section>
</main>
</body>
</html>
```